Business Card Design For A Cajun Seafood Restaurant

We are opening a cajun seafood restaurant in a week. We mainly serve cajun seafood which is orginally from Louisiana. We want design on both sides of a business card. I have menu on the website. You can go to www.reednkettle.example to check out our menu.

Restaurant name: Reed N' Kettle
Phone: +1 (555) 304-7712
Address: 48206 Ludlow Row, #7, Bexmoor Flats, Ca90000
Email: reednkettle@mailbox.example
Website: www.reednkettle.example

Maybe add social media icons (facebook, instagram) if looks nice on the business card.
facebook.com/reednkettle
instagram.com/reednkettle or @reednkettle

Attached is the logo and other business card samples that I like.

```html
<!DOCTYPE html>
<html lang="en">
<head>
<meta charset="utf-8">
<title>Reed N' Kettle — Business Card</title>
<link rel="stylesheet" href="https://fonts.googleapis.com/css2?family=Montserrat:wght@400;500;700&display=swap">
<style>
  :root {
    --backdrop: #e6e7e8;
    --ink: #000000;
    --paper: #ffffff;
    --orange: #f26722;
    --crab-tone: #ee6a25;
    --corn-tone: #f3c21b;
    --text: #111111;
  }
  * { margin: 0; padding: 0; box-sizing: border-box; }
  html, body { width: 1200px; height: 927px; overflow: hidden; }
  body {
    background: var(--backdrop);
    font-family: "Montserrat", sans-serif;
    color: var(--text);
    position: relative;
  }
  .card {
    position: absolute;
    top: 91px;
    width: 424px;
    height: 745px;
    border-radius: 32px;
    overflow: hidden;
    box-shadow: 4px 6px 8px rgba(0,0,0,0.35);
  }
  .card--front { left: 158px; background: var(--paper); }
  .card--back { left: 618px; background: var(--ink); }

  .front__arc { position: absolute; left: 0; top: 0; width: 424px; height: 200px; }

  .illustration {
    position: absolute;
    border-radius: 50%;
  }
  .front__illustration {
    left: 150px; top: 140px; width: 144px; height: 134px;
    background: radial-gradient(circle at 55% 30%, var(--corn-tone) 0 18%, var(--crab-tone) 40%, #c9531b 75%);
  }
  .back__illustration {
    left: 74px; top: 240px; width: 278px; height: 268px;
    background: radial-gradient(circle at 55% 25%, var(--corn-tone) 0 18%, var(--crab-tone) 42%, #b9481a 70%, var(--ink) 72%);
  }

  .brand-name {
    position: absolute; left: 0; right: 0; top: 290px;
    text-align: center;
    font-weight: 700; font-size: 30px;
    color: var(--ink);
    letter-spacing: 0.5px;
  }

  .person { position: absolute; left: 0; right: 0; top: 380px; text-align: center; }
  .person__name { font-weight: 500; font-size: 29px; color: var(--orange); line-height: 34px; }
  .person__role { font-weight: 400; font-size: 18px; line-height: 22px; }

  .rule {
    position: absolute; left: 74px; width: 272px; height: 2px;
    background: linear-gradient(90deg, transparent, var(--ink) 12%, var(--ink) 88%, transparent);
  }
  .rule--top { top: 470px; }
  .rule--bottom { top: 700px; }

  .address {
    position: absolute; left: 0; right: 0; top: 484px;
    text-align: center; font-style: normal;
    font-size: 19px; line-height: 23px;
  }

  .icons {
    position: absolute; left: 0; right: 0; top: 546px;
    display: flex; justify-content: center; gap: 4px;
  }
  .icons svg { width: 14px; height: 14px; }

  .contacts {
    position: absolute; left: 0; right: 0; top: 577px;
    text-align: center; list-style: none;
    font-size: 19px; line-height: 23.2px;
  }
  .accent { color: var(--orange); }

  .stripe { position: absolute; left: 0; bottom: 0; width: 424px; height: 30px; }

  .back__web {
    position: absolute; left: 0; right: 0; top: 666px;
    text-align: center; color: var(--paper);
    font-size: 19px; letter-spacing: 0.5px;
  }
</style>
</head>
<body>

<section class="card card--front" aria-label="Card front">
  <svg class="front__arc" viewBox="0 0 424 200" aria-hidden="true">
    <path d="M0 0 H424 V189 Q212 -30 0 189 Z" fill="var(--ink)"/>
    <path d="M0 189 Q212 -30 424 189" fill="none" stroke="var(--orange)" stroke-width="4"/>
  </svg>

  <div class="illustration front__illustration" role="img" aria-label="Illustration of a cartoon crab holding an ear of corn"></div>
  <div class="brand-name">Reed N' Kettle</div>

  <div class="person">
    <div class="person__name">Marlo Vance</div>
    <div class="person__role">Director</div>
  </div>

  <div class="rule rule--top"></div>

  <address class="address">
    48206 Ludlow Row<br>
    #7, Bexmoor Flats, Ca90000
  </address>

  <div class="icons" aria-hidden="true">
    <svg viewBox="0 0 14 14"><path d="M3 1 L5 4 L4 5.5 Q5.5 8.5 8.5 10 L10 9 L13 11 L11.5 13 Q5 12 1.5 3 Z" fill="none" stroke="var(--orange)" stroke-width="1.2"/></svg>
    <svg viewBox="0 0 14 14"><rect x="1" y="3" width="12" height="8" fill="none" stroke="var(--orange)" stroke-width="1.2"/><path d="M1 3 L7 8 L13 3" fill="none" stroke="var(--orange)" stroke-width="1.2"/></svg>
    <svg viewBox="0 0 14 14"><circle cx="7" cy="7" r="5.8" fill="none" stroke="var(--orange)" stroke-width="1.2"/><ellipse cx="7" cy="7" rx="2.5" ry="5.8" fill="none" stroke="var(--orange)" stroke-width="1"/><path d="M1.2 7 H12.8 M2 4 H12 M2 10 H12" stroke="var(--orange)" stroke-width="0.9"/></svg>
    <svg viewBox="0 0 14 14"><circle cx="7" cy="7" r="5.5" fill="var(--orange)"/></svg>
    <svg viewBox="0 0 14 14"><rect x="1.5" y="1.5" width="11" height="11" fill="var(--orange)"/></svg>
  </div>

  <ul class="contacts">
    <li>+1 (555) 304-7712</li>
    <li>reednkettle@mailbox.example</li>
    <li>www.<span class="accent">reednkettle</span>.example</li>
    <li>facebook.com/reednkettle</li>
    <li>instagram.com/reednkettle</li>
  </ul>

  <div class="rule rule--bottom"></div>

  <svg class="stripe" viewBox="0 0 424 30" aria-hidden="true">
    <rect x="0" y="0" width="424" height="30" fill="var(--ink)"/>
    <rect x="76" y="0" width="273" height="30" fill="var(--paper)"/>
    <rect x="85" y="0" width="255" height="30" fill="var(--orange)"/>
  </svg>
</section>

<section class="card card--back" aria-label="Card back">
  <div class="illustration back__illustration" role="img" aria-label="Large illustration of a cartoon crab holding an ear of corn overhead"></div>

  <div class="back__web">www.<span class="accent">reednkettle</span>.example</div>

  <svg class="stripe" viewBox="0 0 424 30" aria-hidden="true">
    <rect x="0" y="0" width="424" height="30" fill="var(--paper)"/>
    <rect x="75" y="0" width="275" height="30" fill="var(--ink)"/>
    <rect x="85" y="0" width="255" height="30" fill="var(--orange)"/>
  </svg>
</section>

</body>
</html>
```